Bespoke Builders Business Card Design

We need a business card for an established builder of high quality bespoke homes in Auckland and Northland. We build and renovate homes collaboratively facilitating effective communication between owners, builders, architects, suppliers and tradespeople. We have never built or renovated a home that leaks or has faults. We only use reliable materials. We have never been sued or had legal action taken against us. We are honest builders of bespoke homes not group mass produced homes. Our niche market is in character homes. We practice sustainability and have built a lot of coastal property. We have been in business for over thirty years . We would like to see natural colors of the environment sand,sea and maybe vegetation . The design should communicate quality, sustainability,fair pricing, open communication and the originality of bespoke building. And the fact that the builder is registered.

Industry/Entity Type

Business

Contact Information for Business Card

Rowan Tellick Builders
Ph. 021583917
18 Kestrel Rd Harwood Bay Auckland 0814
PO Box 927 Mangawhai 0583

```html
<!DOCTYPE html>
<html lang="en">
<head>
<meta charset="utf-8">
<title>Rowan Tellick Builders – Business Card</title>
<link href="https://fonts.googleapis.com/css2?family=Tinos:wght@400;700&display=swap" rel="stylesheet">
<style>
  :root {
    --page-bg: #e9e6e1;
    --card-white: #fbfbfa;
    --card-black: #0c0c0c;
    --ink: #111111;
    --ink-soft: #2a2a2a;
    --ornament-tone: rgba(17, 17, 17, 0.16);
    --paper-text: #f4f4f4;
  }
  * { box-sizing: border-box; margin: 0; padding: 0; }
  html, body {
    width: 1200px; height: 892px; overflow: hidden;
    background: var(--page-bg);
  }
  .sheet {
    width: 1200px; height: 892px;
    display: flex; flex-direction: column;
    align-items: center; justify-content: center; gap: 40px;
  }
  .card {
    position: relative;
    width: 680px; height: 388px;
    box-shadow: 0 6px 18px rgba(0,0,0,.18);
    overflow: hidden;
  }

  /* Front */
  .card-front { background: var(--card-white); color: var(--ink); }
  .ornament {
    position: absolute; width: 180px; height: 90px;
    background: radial-gradient(closest-side, var(--ornament-tone), rgba(17,17,17,0));
  }
  .ornament-top-left { top: 14px; left: 14px; }
  .ornament-bottom-right { bottom: 14px; right: 14px; }
  .front-name {
    position: absolute; top: 62px; right: 44px;
    font-family: "Tinos", "Times New Roman", serif;
    font-weight: 700; font-size: 42px; letter-spacing: .2px;
    line-height: 1.1; color: var(--ink);
  }
  .front-rule {
    position: absolute; top: 124px; left: 196px; right: 44px;
    height: 4px; background: var(--ink);
  }
  .contact {
    position: absolute; top: 170px; left: 0; right: 0;
    text-align: center; font-style: normal;
    font-family: "Tinos", "Times New Roman", serif;
    font-size: 21px; line-height: 33px; color: var(--ink-soft);
  }

  /* Back */
  .card-back {
    background: linear-gradient(160deg, #1b1b1b 0%, var(--card-black) 55%, #050505 100%);
    display: flex; align-items: center; justify-content: center;
  }
  .back-name {
    font-family: "Tinos", "Times New Roman", serif;
    font-weight: 700; font-size: 46px; letter-spacing: 1px;
    color: var(--paper-text);
  }
</style>
</head>
<body>
  <main class="sheet">
    <section class="card card-front" aria-label="Card front">
      <div class="ornament ornament-top-left" role="img" aria-label="Black floral corner flourish"></div>
      <h1 class="front-name">Rowan Tellick Builders</h1>
      <div class="front-rule"></div>
      <address class="contact">
        021583917<br>
        18 Kestrel Rd Harwood Bay<br>
        Auckland 0814 PO Box 927 Mangawhai 0583
      </address>
      <div class="ornament ornament-bottom-right" role="img" aria-label="Black floral corner flourish"></div>
    </section>

    <section class="card card-back" aria-label="Card back">
      <p class="back-name">Rowan Tellick Builders</p>
    </section>
  </main>
</body>
</html>
```